Business Card Design for my Real Estate Investing Company

This is for a Real Estate Investing Company that will be serving the Las Vegas Valley. Id like the following slogan included: "Investing in Our Community" I have attached my logo. You will see the color tones I'm interested in..in my logo. I would like the card to be double-sided with a modern, professional look.
Target Market(s)
Homeowners, banks, real estate industry
Industry/Entity Type
Real Estate
Contact Information for Business Card
name: Dale Harwick
position: Managing Member
address: 4821 Corliss Pkwy ste 207-300
N. Las Vegas, NV 89084
phone: (702) 555-0143
fax: (702) 555-0187
email: SummitRidgeEstate@hollowmail.test
web: SummitRidgeEstates.test
*At the bottom of the card I would like....
We buy houses for cash....no repairs, no commissions, no fees!
Logo Text
SUMMIT RIDGE ESTATES "Investing in Our Community"
Font styles to use
Other font styles liked:
- Lora
Requirements
Must have
- On the back of the card, i'd like to have my logo large and the following statements:
- Are you considering selling your home? Want a simple, hassle-free transaction? We can help! We buy houses for cash and can close quickly! No need to do any repairs, no realtor commissions, no closing costs.....and no headaches. Let us help you with your real estate needs...!
Nice to have
- multiple colors 2 two tone on front and back

```html
<!DOCTYPE html>
<html lang="en">
<head>
<meta charset="utf-8">
<title>Summit Ridge Estates — Business Card</title>
<link rel="stylesheet" href="https://fonts.googleapis.com/css2?family=Lora:ital,wght@0,700;1,400&family=Open+Sans:wght@400;700&display=swap">
<style>
  :root {
    --stage: #000000;
    --card: #343436;
    --brand-blue: #1b5fb8;
    --ink: #f2f2f2;
    --muted: #c9c9cb;
    --slogan: #8a8a8c;
    --rule: #6a6a6d;
    --icon: #9a9a9e;
  }
  * { margin: 0; padding: 0; box-sizing: border-box; }
  html, body { width: 1200px; height: 900px; overflow: hidden; background: var(--stage); }
  .canvas { position: relative; width: 1200px; height: 900px; font-family: "Open Sans", Arial, sans-serif; }
  .card {
    position: absolute; top: 271px; width: 457px; height: 281px;
    background: var(--card); border-radius: 14px; color: var(--ink);
  }
  .card--front { left: 137px; }
  .card--back { left: 626px; }

  .brand { position: absolute; left: 0; right: 0; top: 352px; top: 80px; text-align: center; }
  .brand__name {
    font-family: "Lora", Georgia, serif; font-weight: 700; font-size: 30px;
    color: var(--brand-blue); letter-spacing: 0.5px; line-height: 1;
    display: inline-flex; align-items: center; gap: 10px;
  }
  .brand__mark { width: 16px; height: 16px; background: var(--brand-blue); display: inline-block; }
  .brand__slogan {
    margin-top: 10px; font-family: "Lora", Georgia, serif; font-style: italic;
    font-size: 13px; letter-spacing: 4px; color: var(--slogan);
  }

  .holder { position: absolute; right: 259px; top: 160px; text-align: right; }
  .holder__name {
    font-family: "Lora", Georgia, serif; font-weight: 700; font-size: 16px;
    color: var(--brand-blue); line-height: 20px;
  }
  .holder__title { font-size: 12.5px; line-height: 18px; color: var(--muted); }
  .holder__address { margin-top: 4px; font-size: 12.5px; line-height: 17px; color: var(--muted); }

  .divider { position: absolute; left: 207px; top: 161px; width: 1px; height: 70px; background: var(--rule); }

  .contacts { position: absolute; left: 212px; top: 165px; list-style: none; }
  .contacts__item { display: flex; align-items: center; gap: 6px; font-size: 12.3px; line-height: 16.5px; color: var(--muted); white-space: nowrap; }
  .contacts__icon { width: 9px; height: 9px; flex: none; }

  .tagline {
    position: absolute; left: 0; right: 0; top: 241px; text-align: center;
    font-weight: 700; font-size: 12.5px; color: #ffffff;
  }

  .pitch {
    position: absolute; left: 0; right: 0; top: 86px; text-align: center;
    font-size: 13.5px; line-height: 18px; color: #ffffff;
  }
</style>
</head>
<body>
<main class="canvas">
  <section class="card card--front" aria-label="Card front">
    <div class="brand">
      <div class="brand__name"><span class="brand__mark"></span>SUMMIT RIDGE ESTATES</div>
      <div class="brand__slogan">"Investing in Our Community"</div>
    </div>

    <div class="holder">
      <div class="holder__name">DALE HARWICK</div>
      <div class="holder__title">Managing Member</div>
      <div class="holder__address">4821 Corliss Pkwy ste 207-300<br>N. Las Vegas, NV 89084</div>
    </div>

    <div class="divider"></div>

    <ul class="contacts">
      <li class="contacts__item">
        <svg class="contacts__icon" viewBox="0 0 10 10" aria-hidden="true"><path d="M1 3 Q5 0 9 3 L8 4.5 L6.5 3.8 L6.5 3 Q5 2.5 3.5 3 L3.5 3.8 L2 4.5 Z M2.5 5 H7.5 L8.5 9 H1.5 Z" fill="var(--icon)"/></svg>
        (702) 555-0143
      </li>
      <li class="contacts__item">
        <svg class="contacts__icon" viewBox="0 0 10 10" aria-hidden="true"><rect x="3" y="1" width="4" height="3" fill="var(--icon)"/><rect x="1" y="4" width="8" height="5" rx="1" fill="var(--icon)"/></svg>
        (702) 555-0187
      </li>
      <li class="contacts__item">
        <svg class="contacts__icon" viewBox="0 0 10 10" aria-hidden="true"><rect x="1" y="2.5" width="8" height="5.5" fill="var(--icon)"/><path d="M1 2.5 L5 5.5 L9 2.5" stroke="var(--card)" stroke-width="0.8" fill="none"/></svg>
        SummitRidgeEstate@hollowmail.test
      </li>
      <li class="contacts__item">
        <svg class="contacts__icon" viewBox="0 0 10 10" aria-hidden="true"><circle cx="5" cy="5" r="4" fill="var(--icon)"/><path d="M1 5 H9 M5 1 Q7.5 5 5 9 M5 1 Q2.5 5 5 9" stroke="var(--card)" stroke-width="0.6" fill="none"/></svg>
        SummitRidgeEstates.test
      </li>
    </ul>

    <p class="tagline">We buy houses for cash....no repairs, no commissions, no fees!</p>
  </section>

  <section class="card card--back" aria-label="Card back">
    <p class="pitch">
      Are you considering selling your home?<br>
      Want a simple, hassle-free transaction? We can help!<br>
      We buy houses for cash and can close quickly!<br>
      No need to do any repairs, no realtor commissions,<br>
      no closing costs.....and no headaches.<br>
      Let us help you with your real estate needs...!
    </p>
  </section>
</main>
</body>
</html>
```